Business card for event manager / organizer "waiter service"

Draft of a new valuable business card for my company.
Events, personnel service providers, festivals

```html
<!DOCTYPE html>
<html lang="de">
<head>
<meta charset="utf-8">
<title>Jonas´ Eventservice – Visitenkarte</title>
<link href="https://fonts.googleapis.com/css2?family=Arimo:wght@400;700&display=swap" rel="stylesheet">
<style>
  :root {
    --stage: #e7e7e7;
    --paper: #ffffff;
    --ink: #0c0c0c;
    --orange: #ee7d1a;
    --grey: #8a8a8a;
    --light: #f2f2f2;
  }
  * { box-sizing: border-box; margin: 0; padding: 0; }
  html, body { width: 1200px; height: 802px; overflow: hidden; }
  body {
    background: var(--stage);
    font-family: "Arimo", Arial, sans-serif;
    position: relative;
  }
  .card {
    position: absolute;
    width: 540px;
    height: 350px;
    overflow: hidden;
    box-shadow: 0 6px 18px rgba(0,0,0,.18);
  }

  /* Front side */
  .card-front { left: 40px; top: 226px; background: var(--paper); }
  .card-front .dark-band {
    position: absolute; left: 0; right: 0; top: 150px; bottom: 0;
    background: var(--ink);
  }
  .card-front .portrait {
    position: absolute; left: 24px; top: 58px; width: 210px; height: 292px;
    background: linear-gradient(180deg, #6b5a4c 0%, #3a302a 35%, #141820 70%, #0e1118 100%);
    border-radius: 90px 90px 0 0;
  }
  .brand { display: flex; align-items: center; gap: 10px; }
  .brand-mark { width: 30px; height: 30px; background: var(--orange); flex: none; }
  .brand-name { font-weight: 700; font-size: 25px; letter-spacing: .3px; }
  .card-front .brand-block { position: absolute; right: 28px; top: 22px; text-align: right; }
  .card-front .brand-name { color: var(--ink); }
  .tagline { font-size: 10px; color: var(--grey); margin-top: 4px; }
  .owner { position: absolute; right: 28px; top: 86px; text-align: right; }
  .owner-name { color: var(--orange); font-weight: 700; font-size: 24px; }
  .owner-role { color: var(--grey); font-size: 14px; margin-top: 2px; }
  .contacts {
    position: absolute; right: 28px; top: 164px;
    list-style: none; color: var(--light); font-size: 14px; line-height: 21px;
  }
  .contacts li { display: flex; justify-content: flex-end; align-items: center; gap: 8px; }
  .contacts svg { width: 13px; height: 13px; flex: none; }
  .address-strip {
    position: absolute; right: 0; bottom: 22px; width: 300px; height: 42px;
    background: var(--orange); color: var(--paper); font-size: 15px;
    display: flex; align-items: center; justify-content: flex-end; padding-right: 28px;
  }

  /* Back side */
  .card-back {
    left: 620px; top: 226px;
    background: linear-gradient(180deg, #3a3a3a 0%, #1c1c1c 45%, #140d08 100%);
  }
  .card-back .crowd {
    position: absolute; left: 0; right: 0; bottom: 0; height: 220px;
    background:
      radial-gradient(ellipse at 70% 30%, rgba(245,150,70,.85) 0%, rgba(200,90,40,.55) 35%, rgba(60,20,10,0) 70%),
      linear-gradient(180deg, rgba(30,20,15,0) 0%, #7a3418 55%, #3b140a 100%);
  }
  .card-back .brand-block {
    position: absolute; left: 0; right: 0; top: 70px;
    display: flex; flex-direction: column; align-items: center;
  }
  .card-back .brand-mark { width: 44px; height: 44px; }
  .card-back .brand-name { color: var(--paper); font-size: 38px; }
  .card-back .tagline { color: #d8d8d8; font-size: 13px; margin-top: 8px; }
</style>
</head>
<body>

<section class="card card-front">
  <div class="dark-band"></div>
  <div class="portrait" role="img" aria-label="Porträtfoto des Inhabers in dunklem Hemd"></div>

  <div class="brand-block">
    <div class="brand">
      <span class="brand-mark"></span>
      <span class="brand-name">Jonas´ Eventservice</span>
    </div>
    <p class="tagline">..denn die nächste Feier kommt bestimmt!</p>
  </div>

  <div class="owner">
    <p class="owner-name">Jonas Brenneke</p>
    <p class="owner-role">Inhaber</p>
  </div>

  <ul class="contacts">
    <li>02361 555 01 27
      <svg viewBox="0 0 16 16"><circle cx="8" cy="8" r="8" fill="#ee7d1a"/><path d="M5 4.5c.6-.5 1.2-.3 1.5.3l.6 1.2c.2.4 0 .8-.3 1l-.5.4c.4 1 1.1 1.7 2.1 2.1l.4-.5c.3-.3.7-.4 1-.2l1.2.6c.6.3.7.9.3 1.5-1 1.2-3.3.4-4.9-1.2S3.8 5.5 5 4.5z" fill="#0c0c0c"/></svg>
    </li>
    <li>0151 555 40 18
      <svg viewBox="0 0 16 16"><circle cx="8" cy="8" r="8" fill="#ee7d1a"/><rect x="5.5" y="3.5" width="5" height="9" rx="1" fill="#0c0c0c"/></svg>
    </li>
    <li>info@jonas-eventservice.de
      <svg viewBox="0 0 16 16"><rect x="1" y="3" width="14" height="10" fill="#ee7d1a"/><path d="M1 3l7 6 7-6" fill="none" stroke="#0c0c0c" stroke-width="1.3"/></svg>
    </li>
    <li>www.jonas-eventservice.de
      <svg viewBox="0 0 16 16"><circle cx="8" cy="8" r="7" fill="none" stroke="#ee7d1a" stroke-width="2"/></svg>
    </li>
    <li>jonaseventservice
      <svg viewBox="0 0 16 16"><rect x="1" y="1" width="14" height="14" fill="#ee7d1a"/></svg>
    </li>
  </ul>

  <div class="address-strip">Lindenweg 14, 48100 Musterstadt</div>
</section>

<section class="card card-back">
  <div class="crowd" role="img" aria-label="Feiernde Menge mit erhobenen Händen im orangen Bühnenlicht"></div>
  <div class="brand-block">
    <div class="brand">
      <span class="brand-mark"></span>
      <span class="brand-name">Jonas´ Eventservice</span>
    </div>
    <p class="tagline">..denn die nächste Feier kommt bestimmt!</p>
  </div>
</section>

</body>
</html>
```